Willow Cradle Pregnancy and Baby Massage

I need a web design for a new business, WILLOW CRADLE PREGNANCY AND BABY MASSAGE that I am in the process of setting up in the suburbs of Perth, Western Australia. The business is owned and operated by myself and my intention is to service Pregnant Mothers and Parents of Young Babies that would benefit from massage. I would like to have a "Home Page" and pages for "About Me", "Pregnancy Massage", "Baby Massage", a Pricing Page for Pregnancy Massage Sessions, a Pricing Page for Baby Massage Sessions, and a "Contact Me" page to allow clients to either contact me with queries or book available pregnancy massage sessions on a particular day of the week. I would also like a "News" page that would include articles I have written, news about new courses and a link to my Facebook page (yet to be set up). I would like to keep the colour schemes similar to my logo design colours. I need the design to be easy to follow and to appeal to a younger audience (20's to mid 30's).
The target audience is pregnant mothers-to-be wishing to receive massage treatments, and new parents and grandparents of small babies that would like to learn how to massage their babies.
The look and feel should be modern, professional, elegant and feminine.
I need the design to be in a standard format such that I can update the content by myself ( and does not need specialised software) as the company and business progresses.

Target Market(s)

Contact Information for Business Card

Card should have rounded edges. Design should have the same "feel" as the website. Contact Details of my business address, mobile phone, email and website should be included.

Font styles to use
Script

Requirements
Must have
• Same colours as logo design. In cmyk system, the colours are: 20,60,0,0 which best result is pantone 681 and 40,40,0,0 which best result is pantone 2645. Card should include the logo design.

```html
<!DOCTYPE html>
<html lang="en">
<head>
<meta charset="utf-8">
<title>About Me – Willow Cradle Pregnancy and Baby Massage</title>
<link href="https://fonts.googleapis.com/css2?family=Lato:wght@300;400;700&display=swap" rel="stylesheet">
<style>
  :root {
    --lavender: #a198c6;
    --orchid: #b466a8;
    --page: #f7f7f7;
    --footer: #f0f0f0;
    --text: #6f6f6f;
    --link: #7a7a7a;
    --white: #ffffff;
    --icon: #bdbdbd;
  }
  * { margin: 0; padding: 0; box-sizing: border-box; }
  html, body { width: 1200px; height: 1198px; overflow: hidden; }
  body {
    position: relative;
    background: var(--page);
    font-family: "Lato", sans-serif;
    color: var(--text);
  }
  .top-bar {
    position: absolute; left: 0; top: 0; width: 1200px; height: 84px;
    background: var(--lavender);
  }
  .brand-tab {
    position: absolute; left: 147px; top: 0; width: 275px; height: 178px;
    background: var(--white);
    clip-path: polygon(0 0, 100% 0, 100% 152px, 50% 178px, 0 152px);
    display: flex; flex-direction: column; align-items: center; justify-content: center;
    padding-bottom: 24px; gap: 8px;
  }
  .brand-mark { width: 34px; height: 34px; border-radius: 50%; background: var(--orchid); }
  .brand-name {
    font-size: 20px; font-weight: 700; color: var(--orchid);
    text-align: center; line-height: 1.2;
  }
  .menu-toggle { position: absolute; left: 1019px; top: 32px; }
  .page-title {
    position: absolute; left: 147px; top: 198px;
    font-size: 37px; font-weight: 700; color: var(--orchid);
  }
  .copy {
    position: absolute; left: 147px; width: 906px;
    font-size: 14.2px; line-height: 22.4px; font-weight: 400;
  }
  .copy-intro { top: 260px; }
  .copy-career { top: 327px; }
  .copy-closing { top: 912px; }
  .feature-photo {
    position: absolute; left: 147px; top: 431px; width: 906px; height: 466px;
    background: linear-gradient(100deg, #f3eeee 0%, #e9c2a6 35%, #f1d4c3 60%, #f6efee 100%);
  }
  .site-footer {
    position: absolute; left: 0; top: 1010px; width: 1200px; height: 188px;
    background: var(--footer);
  }
  .cert-badge {
    position: absolute; left: 158px; top: 1036px; width: 258px; height: 146px;
    border-radius: 10px; background: #e6dbe8;
  }
  .footer-heading {
    position: absolute; top: 1034px;
    font-size: 22px; font-weight: 700; color: var(--orchid);
  }
  .quick-links { left: 473px; }
  .follow { left: 877px; }
  .link-list { position: absolute; top: 1073px; list-style: none; }
  .link-list li { font-size: 13px; line-height: 25.6px; color: var(--link); }
  .links-a { left: 474px; }
  .links-b { left: 662px; }
  .social { position: absolute; left: 874px; top: 1070px; display: flex; gap: 10px; }
  .social span { width: 32px; height: 32px; border-radius: 50%; background: var(--icon); }
  .copyright { position: absolute; left: 874px; top: 1119px; font-size: 12.5px; color: var(--link); }
</style>
</head>
<body>
  <header class="top-bar"></header>
  <div class="brand-tab">
    <span class="brand-mark"></span>
    <div class="brand-name">Willow Cradle<br>Pregnancy and Baby Massage</div>
  </div>
  <svg class="menu-toggle" width="31" height="20" viewBox="0 0 31 20" aria-label="Menu">
    <rect y="0" width="31" height="3" fill="#fff"/>
    <rect y="8.5" width="31" height="3" fill="#fff"/>
    <rect y="17" width="31" height="3" fill="#fff"/>
  </svg>

  <h1 class="page-title">About Me</h1>
  <p class="copy copy-intro">Maren is a Practitioner of Pregnancy Massage, and a Paediatric Massage Consultant. She completed her training with Prenatal Touch Academy, and the Little Steps Infant Massage Institute. The LSIMI is endorsed by the Southern Guild of Midwives.</p>
  <p class="copy copy-career">The Coastal Natural Therapies Society, and accredited by the Guild of Touch Therapists.Maren is also a Registered Nurse and Midwife. Most of her professional career has been as a midwife, which has included working in the community in the UK, providing ante natal care and classes, intra partum care, home births, and postnatal care in the home. Maren has also worked in the private and public maternity sectors in Perth.</p>
  <div class="feature-photo" role="img" aria-label="Photo of hands gently massaging a baby's back on a white blanket"></div>
  <p class="copy copy-closing">Maren was introduced to the wonderful benefits of pregnancy and baby massage after a career change. Working as a Practitioner of Pregnancy Massage, and Paediatric Massage Consultant, enables her to continue working with mothers and babies.</p>

  <footer class="site-footer"></footer>
  <div class="cert-badge" role="img" aria-label="Certification badge"></div>
  <h2 class="footer-heading quick-links">Quick Links</h2>
  <ul class="link-list links-a">
    <li>Home</li><li>About Me</li><li>Benefits of Pregnancy</li><li>Benefits of Baby Massage</li>
  </ul>
  <ul class="link-list links-b">
    <li>Pregnancey Massage Sessions</li><li>Baby Massage Sessions</li><li>Contact</li>
  </ul>
  <h2 class="footer-heading follow">Follow Us</h2>
  <div class="social" aria-label="Social links"><span></span><span></span><span></span><span></span></div>
  <p class="copyright">© 2017 Willow Cradle Pregnancy</p>
</body>
</html>
```